Feature Film "look book" digital brochure

Looking for a designer to create an edgy, gritty, eye popping visual representation of my film to get interest from investors, producers and actors. Basically it would introduce the project and in about 7-9 pages; give an overview of the film, why to invest, an artistic statement and potential casting ideas and an introduction to the key crew. I have included way more images than you would ever need in the files. I've also included samples for other films and a brochure someone already did for the film just to give you an idea of how it should be structured and the text content. Visually that piece is not a good guideline because it doesn't visually rep the film which is why I"m doing this contest!
The film is called 3 by 12: the sentence of an alcoholic teacher who commits a crime she can't remember and whose chance for survival depends on an ex-drug dealer and a basketball court.
Reason: I wanted people to have more time to send samples
Independent film investors, artists
Digital

```html
<!DOCTYPE html>
<html lang="en">
<head>
<meta charset="utf-8">
<title>3 by 12 — Key Crew</title>
<link rel="stylesheet" href="https://fonts.googleapis.com/css2?family=Cabin:wght@400&family=Rubik:wght@700&display=swap">
<style>
  :root {
    --ink: #000000;
    --paper: #ffffff;
    --accent: #ed1c24;
  }
  html, body {
    margin: 0;
    padding: 0;
    overflow: hidden;
    background: var(--paper);
  }
  .page {
    position: relative;
    width: 1200px;
    height: 1200px;
    box-sizing: border-box;
    border: 1px solid var(--ink);
    background: var(--paper);
    overflow: hidden;
    font-family: "Cabin", sans-serif;
    color: var(--ink);
  }
  .bars {
    position: absolute;
    inset: 0;
  }
  .section-title {
    position: absolute;
    left: 385px;
    top: 52px;
    width: 450px;
    margin: 0;
    text-align: center;
    font-family: "Rubik", sans-serif;
    font-weight: 700;
    font-size: 76px;
    line-height: 76px;
    white-space: nowrap;
  }
  .film-title {
    position: absolute;
    left: 385px;
    width: 450px;
    margin: 0;
    text-align: center;
    font-family: "Rubik", sans-serif;
    font-weight: 700;
    font-size: 330px;
    line-height: 1;
    letter-spacing: -10px;
    white-space: nowrap;
  }
  .film-title--top { top: 158px; }
  .film-title--mid { top: 473px; transform: scaleX(0.86); }
  .film-title--low { top: 805px; }
  .crew-list {
    position: absolute;
    top: 339px;
    margin: 0;
    padding: 0;
    list-style: none;
    font-size: 19.5px;
    line-height: 25.4px;
  }
  .crew-list--left { left: 115px; }
  .crew-list--right { left: 904px; }
  .page-tag {
    position: absolute;
    left: 0;
    bottom: 0;
    width: 280px;
    height: 70px;
    background: var(--accent);
    color: var(--paper);
    font-size: 35px;
    line-height: 70px;
    padding-left: 36px;
    box-sizing: border-box;
  }
</style>
</head>
<body>
  <main class="page">
    <svg class="bars" width="1200" height="1200" viewBox="0 0 1200 1200" aria-hidden="true">
      <g fill="var(--ink)">
        <rect x="385" y="43" width="450" height="6"/>
        <rect x="385" y="124" width="450" height="6"/>
        <rect x="385" y="145" width="450" height="36" rx="4"/>
        <rect x="385" y="462" width="450" height="35" rx="4"/>
        <rect x="385" y="777" width="450" height="35" rx="4"/>
        <rect x="385" y="1107" width="450" height="37" rx="4"/>
      </g>
    </svg>

    <h1 class="section-title">KEY CREW</h1>

    <p class="film-title film-title--top">3</p>
    <p class="film-title film-title--mid">BY</p>
    <p class="film-title film-title--low">12</p>

    <ul class="crew-list crew-list--left">
      <li>Nola Ferrante</li>
      <li>Cally Gaston</li>
      <li>Lashonda Kimble</li>
      <li>Tessa Slade</li>
      <li>Annaliese Furukawa</li>
      <li>Lauren Dupont</li>
      <li>Joelle Sabo</li>
      <li>Rena Rothwell</li>
      <li>Holden Brannigan</li>
      <li>Cora Pemberton</li>
      <li>Dario Bravo</li>
      <li>Chantal Marchand</li>
      <li>Lesley Harwell</li>
      <li>Simone Stanfield</li>
      <li>Tamsin Cowley</li>
      <li>Bette Rizzo</li>
      <li>Sadie Pappas</li>
      <li>Myrna Gable</li>
      <li>Maryann Dorval</li>
      <li>Mirela Schulte</li>
    </ul>

    <ul class="crew-list crew-list--right">
      <li>Lena Quill</li>
      <li>Elaine Rudd</li>
      <li>Leona Romano</li>
      <li>Margo Tierney</li>
      <li>Alina Constance</li>
      <li>Brenda Arlen</li>
      <li>Sarah Scharf</li>
      <li>Greta Vanhorn</li>
      <li>Liesel Garrow</li>
      <li>Alyssa Doucet</li>
      <li>Martin Bolton</li>
      <li>Oma Exley</li>
      <li>Britt Hasselt</li>
      <li>Wade Smithers</li>
      <li>Marlene Pakradian</li>
      <li>Selene Hillard</li>
      <li>Shannon Tyner</li>
      <li>Gabriella Rohrback</li>
      <li>Adriana Hagedorn</li>
      <li>Stefanie Dickerson</li>
    </ul>

    <div class="page-tag">key crew</div>
  </main>
</body>
</html>
```